HOT TUB - SPAS service needs an business card

I need an business for my company who his specialise in a maintenance,water treatment and cleaning of Hot Tub - Spas for commercial and residential customers. The company operate mainly in the ski resort of Chamonix, Megève and St Gervais. The final product should communicate pure water, cleanest and professional for luxury property's.
I have upload a logo but any improvement on it is welcome.(color,size, details etc..) or any other idea. Thank you
Company Name: 58 BAINS
My name: Lucien Marchetti
Email: lucimarch@examplemail.net
Tel: +33 (0)6 71 58 29 64
Description to be on the card in french(first langage) and in English:
- Spas service
- Entretien, traitement eau, nettoyage.
- Maintenance, water treatment, cleaning.
Industry/Entity Type
Residential
Colors
Designer to choose colors to be used in the design.
Look and feel
Each slider illustrates characteristics of the customer's brand and the style your logo design should communicate.

```html
<!DOCTYPE html>
<html lang="fr">
<head>
<meta charset="utf-8">
<title>58 BAINS – Business card</title>
<link href="https://fonts.googleapis.com/css2?family=Open+Sans:wght@400;600;700&display=swap" rel="stylesheet">
<style>
  :root {
    --page-bg: #ece9e4;
    --water-light: #3ea6f5;
    --water-mid: #2290ec;
    --water-deep: #1a7ddc;
    --band-blue: #1463c4;
    --stripe: #9fd2ff;
    --ink: #ffffff;
  }
  * { margin: 0; padding: 0; box-sizing: border-box; }
  html, body {
    width: 1200px; height: 1133px; overflow: hidden;
    background: var(--page-bg);
    font-family: "Open Sans", Arial, sans-serif;
    color: var(--ink);
  }
  .canvas { position: relative; width: 1200px; height: 1133px; }
  .card {
    position: absolute; width: 888px; height: 507px; overflow: hidden;
    box-shadow: 0 4px 14px rgba(0,0,0,.18);
  }
  .card--front { left: 52px; top: 35px; }
  .card--back { left: 252px; top: 579px; }
  .water-surface {
    position: absolute; inset: 0;
    background:
      radial-gradient(ellipse at 70% 20%, rgba(255,255,255,.14), transparent 55%),
      radial-gradient(ellipse at 15% 85%, rgba(0,60,150,.18), transparent 60%),
      linear-gradient(160deg, var(--water-light), var(--water-mid) 50%, var(--water-deep));
  }
  .brand-mark {
    position: absolute; left: 0; right: 0; text-align: center;
    font-weight: 600; letter-spacing: 2px;
  }
  .card--front .brand-mark { top: 95px; font-size: 44px; }
  .card--back .brand-mark { top: 150px; font-size: 50px; }
  .company-name {
    position: absolute; top: 224px; left: 0; right: 0; text-align: center;
    font-weight: 600; font-size: 39px;
  }
  .contact {
    position: absolute; left: 0; right: 0; text-align: center;
    font-size: 26px; display: flex; justify-content: center; align-items: center; gap: 12px;
  }
  .contact svg { width: 24px; height: 24px; fill: var(--ink); }
  .contact--phone { top: 322px; }
  .contact--email { top: 368px; }
  .stripe { position: absolute; left: 0; right: 0; top: 441px; height: 3px; background: var(--stripe); }
  .name-band {
    position: absolute; left: 0; right: 0; top: 448px; bottom: 0;
    background: var(--band-blue);
    display: flex; align-items: center; justify-content: center;
    font-weight: 700; font-size: 28px;
  }
  .services-title {
    position: absolute; top: 352px; left: 0; right: 0; text-align: center;
    font-weight: 600; font-size: 30px;
  }
  .services-line {
    position: absolute; left: 0; right: 0; text-align: center; font-size: 29px;
  }
  .services-line--fr { top: 404px; }
  .services-line--en { top: 445px; }
</style>
</head>
<body>
<main class="canvas">
  <section class="card card--front">
    <div class="water-surface" role="img" aria-label="Water droplets on a blue surface"></div>
    <div class="brand-mark">58 BAINS</div>
    <div class="company-name">58 BAINS</div>
    <div class="contact contact--phone">
      <svg viewBox="0 0 24 24" aria-hidden="true"><path d="M6.6 10.8a15.1 15.1 0 0 0 6.6 6.6l2.2-2.2a1 1 0 0 1 1-.25 11.4 11.4 0 0 0 3.6.57 1 1 0 0 1 1 1V20a1 1 0 0 1-1 1A17 17 0 0 1 3 4a1 1 0 0 1 1-1h3.5a1 1 0 0 1 1 1c0 1.25.2 2.45.57 3.57a1 1 0 0 1-.25 1z"/></svg>
      <span>+33 (0)6 71 58 29 64</span>
    </div>
    <div class="contact contact--email">
      <svg viewBox="0 0 24 24" aria-hidden="true"><path d="M2 6h20v13H2z M3.5 7.5 12 13l8.5-5.5" fill="none" stroke="#fff" stroke-width="2"/></svg>
      <span>lucimarch@examplemail.net</span>
    </div>
    <div class="stripe"></div>
    <div class="name-band">Lucien Marchetti</div>
  </section>

  <section class="card card--back">
    <div class="water-surface" role="img" aria-label="Water droplets on a blue surface"></div>
    <div class="brand-mark">58 BAINS</div>
    <div class="services-title">SPAS SERVICES</div>
    <div class="services-line services-line--fr">• Entretien &nbsp;• traitement eau &nbsp;• nettoyage</div>
    <div class="services-line services-line--en">• Maintenance &nbsp;• water treatment &nbsp;• cleaning.</div>
  </section>
</main>
</body>
</html>
```